BRIGHTWATER RV Resort needs a logo and advertising poster

We need an advertising poster for our epic RV Resort located on north end of Tillon Lake, (Northern Saskatchewan, trees no mountains)
SEASONAL FULL SERVICE SITES with marina and lake access.
Sauna/plunge, disc golf , hiking/quad trails, and pet friendly.
We are after a fun 70,s themed simple poster. Please use brand guide for colours and redo logo to be Brightwater Resort.

Target Market(s)

RV owners looking for permeant sites. No tenting.

Font styles to use
Other font styles liked:
• See brand guide

Requirements
Must have
• Change exisiting branding to BRIGHTWATER RESORT instead of coffee Emphasis Limited sites.... Referral discount. Phone number.
Nice to have
• .
Should not have
• Keep it simple

```html
<!DOCTYPE html>
<html lang="en">
<head>
<meta charset="utf-8">
<title>Brightwater Resort – Poster</title>
<link href="https://fonts.googleapis.com/css2?family=Oswald:wght@500;600;700&family=Kaushan+Script&family=Lexend:wght@400;600;700;800&display=swap" rel="stylesheet">
<style>
  :root {
    --backdrop: #7a7868;
    --paper: #f4f1e4;
    --forest: #6d8c4c;
    --forest-dark: #5d7c40;
    --navy: #14303d;
    --cream: #f5f0dc;
    --sun: #f5b731;
    --sun-deep: #e48a2a;
    --sky-blue: #8fb8bf;
    --pine: #2f5560;
    --pine-dark: #21424d;
  }
  * { margin: 0; padding: 0; box-sizing: border-box; }
  html, body { width: 1200px; height: 2308px; overflow: hidden; }
  body { background: var(--backdrop); position: relative; font-family: "Lexend", sans-serif; }

  .poster {
    position: absolute; left: 80px; top: 419px;
    width: 1040px; height: 1470px;
    background: var(--paper);
    box-shadow: 0 18px 40px rgba(0,0,0,.35);
  }
  .poster-field {
    position: absolute; inset: 28px;
    background: radial-gradient(ellipse at 50% 45%, var(--forest) 55%, var(--forest-dark) 100%);
    border-radius: 14px;
  }
  .abs { position: absolute; }

  .scene-art {
    left: 117px; top: 345px; width: 790px; height: 680px;
    border-radius: 48% 48% 14px 14px / 36% 36% 14px 14px;
    background: linear-gradient(180deg,
      var(--sun) 0%, var(--sun-deep) 30%, var(--sky-blue) 52%,
      var(--pine) 78%, var(--pine-dark) 100%);
  }

  .title-main {
    left: 0; right: 0; top: 78px; text-align: center;
    font-family: "Oswald", sans-serif; font-weight: 600;
    font-size: 150px; line-height: 1; letter-spacing: 1px;
    color: var(--cream);
  }
  .title-script {
    left: 40px; right: 0; top: 210px; text-align: center;
    font-family: "Kaushan Script", "Oswald", sans-serif; font-size: 120px; line-height: 1;
    color: var(--navy);
    transform: rotate(-6deg);
  }

  .location {
    left: 0; right: 0; top: 1058px; text-align: center;
    color: var(--cream); white-space: nowrap;
  }
  .location-label { font-weight: 700; font-size: 34px; letter-spacing: .5px; vertical-align: middle; }
  .location-pin { width: 36px; height: 48px; vertical-align: middle; margin: 0 6px 0 18px; }
  .location-lake { font-weight: 800; font-size: 54px; letter-spacing: 1.5px; vertical-align: middle; }

  .site-band {
    left: 80px; right: 80px; top: 1122px; height: 40px;
    background: var(--navy); color: var(--cream);
    font-weight: 700; font-size: 22px; line-height: 40px; text-align: center;
    letter-spacing: .3px; white-space: nowrap;
  }

  .brand-mark { left: 62px; top: 1210px; width: 230px; text-align: center; color: var(--cream); }
  .brand-mark-square { width: 26px; height: 26px; background: var(--cream); margin: 0 auto 10px; }
  .brand-mark-name { font-weight: 700; font-size: 28px; letter-spacing: .5px; }
  .brand-note {
    left: 62px; top: 1350px; width: 230px; text-align: center;
    color: var(--navy); font-weight: 600; font-size: 12px; line-height: 1.15;
  }

  .divider { left: 302px; top: 1196px; width: 2px; height: 198px; background: var(--cream); }

  .provide-heading { left: 332px; top: 1180px; font-weight: 800; font-size: 30px; color: var(--navy); }
  .amenity-list { list-style: none; color: var(--cream); font-size: 24px; line-height: 33px; }
  .amenity-list li { display: flex; align-items: center; gap: 10px; white-space: nowrap; }
  .amenity-list svg { width: 22px; height: 22px; flex: none; }
  .amenities-left { left: 332px; top: 1218px; }
  .amenities-right { left: 665px; top: 1218px; }

  .referral { left: 332px; top: 1328px; display: flex; align-items: center; gap: 12px; }
  .referral-value { font-family: "Oswald", sans-serif; font-weight: 700; font-size: 66px; line-height: 1; color: var(--sun); }
  .referral-label { font-family: "Oswald", sans-serif; font-weight: 700; font-size: 28px; line-height: 1; color: var(--navy); }

  .contact { right: 80px; top: 1326px; text-align: right; }
  .contact-phone { font-family: "Oswald", sans-serif; font-weight: 700; font-size: 34px; line-height: 1.1; color: var(--sun); letter-spacing: .5px; }
  .contact-web { font-family: "Oswald", sans-serif; font-weight: 600; font-size: 25px; color: var(--navy); }
</style>
</head>
<body>
  <main class="poster">
    <div class="poster-field"></div>

    <div class="abs scene-art" role="img" aria-label="Retro 70s illustration of a large setting sun behind a peak, pine forest, a tent and a vintage camper van"></div>

    <h1 class="abs title-main">BRIGHTWATER</h1>
    <div class="abs title-script">Resort</div>

    <div class="abs location">
      <span class="location-label">LOCATED ON</span><svg class="location-pin" viewBox="0 0 24 32" aria-hidden="true"><path d="M12 0C5.4 0 0 5.2 0 11.6 0 20 12 32 12 32s12-12 12-20.4C24 5.2 18.6 0 12 0z" fill="#f5b731"/><circle cx="12" cy="11.5" r="5" fill="#6d8c4c"/></svg><span class="location-lake">TILLON LAKE</span>
    </div>

    <div class="abs site-band">NORTHERN SASKATCHEWAN LARGER SEASONAL SITES &amp; LIMITED SITES</div>

    <div class="abs brand-mark">
      <div class="brand-mark-square"></div>
      <div class="brand-mark-name">BRIGHTWATER</div>
    </div>
    <div class="abs brand-note">Brand Guide<br>NOVEMBER 2021</div>

    <div class="abs divider"></div>

    <h2 class="abs provide-heading">WE PROVIDE</h2>
    <ul class="abs amenity-list amenities-left">
      <li><svg viewBox="0 0 24 24"><path d="M3 13l6 6L21 5" fill="none" stroke="#14303d" stroke-width="3.5" stroke-linecap="round"/></svg>Marina &amp; lake access</li>
      <li><svg viewBox="0 0 24 24"><path d="M3 13l6 6L21 5" fill="none" stroke="#14303d" stroke-width="3.5" stroke-linecap="round"/></svg>Sauna or plunge</li>
      <li><svg viewBox="0 0 24 24"><path d="M3 13l6 6L21 5" fill="none" stroke="#14303d" stroke-width="3.5" stroke-linecap="round"/></svg>Disc golf</li>
    </ul>
    <ul class="abs amenity-list amenities-right">
      <li><svg viewBox="0 0 24 24"><path d="M3 13l6 6L21 5" fill="none" stroke="#14303d" stroke-width="3.5" stroke-linecap="round"/></svg>Hiking or quad trails</li>
      <li><svg viewBox="0 0 24 24"><path d="M3 13l6 6L21 5" fill="none" stroke="#14303d" stroke-width="3.5" stroke-linecap="round"/></svg>Pet friendly.</li>
    </ul>

    <div class="abs referral">
      <span class="referral-value">10%</span>
      <span class="referral-label">REFERRAL<br>DISCOUNT</span>
    </div>

    <div class="abs contact">
      <div class="contact-phone">1-306-555-0148</div>
      <div class="contact-web">brightwaterrv.com</div>
    </div>
  </main>
</body>
</html>
```